International online gaming platform needs a game UI design

1. We need a game interface for three kinds of theme based on our guideline and sample mockup.
2. The product type is the online casino games related, we need a series of casino games UIs, however, we can start on the game lobby first.
3. Three theme you might choose from or refer to:
A. 3D look & feel
B. Realistic casino theme
C. Richness and grandeur
D. European casino style
4. NOT ALLOWED to change the design layout.
MUST follow our sample mock up and ONLY redefine the design style.
5. All items must be in a stand-alone component, eg. Button, Tab, Icon,... etc.
6. We need the layout in vector shape, but we can review in JPG or PNG format.
7. The image size: 1366 x 768

Updated:
1. All items and their positions should be same as the sample UI we provided.
Please redesign all the items and create a new theme for it.
No need to create a new layout.
2. Although we accept the draft design, but all the items in UI should be completed.
3. All the wordings in the sample UI are confirmed, you might change the fonts.
4. For the avatar in the left hand side, you don't have to redraw it.
We already have our own avatar system implemented.
5. All the items such as icons, tabs, and buttons are free to redesign.

Dear designers,

We've increased our budget and raise the prize money to 800 USD.  
We also accept the draft design in PNG format and we can go through the details in handover stage.
Thank you very much. 

Reason: Dear designers, We decided to extend the deadline by 7 days. As mentioned in the task description, we are looking for a new style of design and you might refer to the below style. A. 3D look & feel B. Realistic casino theme C. Richness and grandeur D. European casino style If you are still interested in our project, please send us your work. Thank you very much!

```html
<!DOCTYPE html>
<html lang="en">
<head>
<meta charset="utf-8">
<title>Live Casino Lobby</title>
<link href="https://fonts.googleapis.com/css2?family=Cinzel:wght@900&family=Roboto:ital,wght@0,400;0,500;0,700;1,700&display=swap" rel="stylesheet">
<style>
:root{
  --felt-1:#1d8a45;
  --felt-2:#0f5a2a;
  --felt-3:#05250f;
  --lacquer:#0b0d0c;
  --lacquer-2:#1d201f;
  --gold-hi:#fff1b0;
  --gold:#e9b93a;
  --gold-mid:#c48a1c;
  --gold-dark:#6e4708;
  --sapphire-hi:#7fa8ff;
  --sapphire:#2a4fc7;
  --sapphire-dark:#0f1f6b;
  --emerald-hi:#8fe27a;
  --emerald:#2f9a3a;
  --emerald-dark:#0f5018;
  --ruby-hi:#ff8f80;
  --ruby:#c72a1e;
  --ruby-dark:#6e0c06;
  --silver-hi:#ffffff;
  --silver:#d4d8dc;
  --silver-dark:#7d848b;
  --grid:#b9cfe6;
  --yellow:#f6e11e;
  --skin:#f7c998;
  --text-light:#ffffff;
  --text-dark:#1b1b1b;
}
*{box-sizing:border-box;margin:0;padding:0}
html,body{width:1200px;height:675px;overflow:hidden;background:#000}
body{font-family:"Roboto",Arial,sans-serif;color:var(--text-light)}

.lobby{position:relative;width:1200px;height:675px;overflow:hidden;
  background:
    radial-gradient(ellipse 620px 260px at 640px 330px,rgba(0,0,0,.55),transparent 75%),
    radial-gradient(ellipse 900px 500px at 640px 500px,var(--felt-1),var(--felt-2) 60%,var(--felt-3) 100%)}
.abs{position:absolute}

/* gold rim used by framed components */
.gold-rim{border:2px solid var(--gold);box-shadow:0 0 0 1px var(--gold-dark),inset 0 0 0 1px var(--gold-hi),0 4px 10px rgba(0,0,0,.6)}

/* header */
.brand{left:4px;top:4px;width:337px;height:33px;display:flex;align-items:center;gap:10px;padding-left:10px;
  background:linear-gradient(#26221a,#050505);border-radius:3px}
.brand-dot{width:17px;height:17px;border-radius:50%;background:var(--gold)}
.brand-name{font-family:"Cinzel",Georgia,serif;font-weight:900;font-size:24px;color:var(--gold);letter-spacing:1px}
.clock{left:18px;top:44px;width:165px;height:26px;border-radius:7px;font-size:10px;display:flex;align-items:center;justify-content:center;
  background:linear-gradient(#2b2b2b,#050505);border:1px solid var(--gold-mid);box-shadow:inset 0 1px 0 rgba(255,255,255,.15)}

.tool{top:4px;width:33px;height:33px;border-radius:6px;display:flex;align-items:center;justify-content:center;
  background:linear-gradient(var(--sapphire-hi),var(--sapphire) 50%,var(--sapphire-dark));
  border:2px solid var(--gold);box-shadow:inset 0 1px 0 rgba(255,255,255,.6),0 3px 6px rgba(0,0,0,.6)}
.tool.close{background:linear-gradient(var(--ruby-hi),var(--ruby) 50%,var(--ruby-dark))}

/* game tabs */
.tab{top:45px;height:40px;border-radius:16px;display:flex;align-items:center;justify-content:center;
  font-size:19px;font-weight:700;padding-left:46px;text-shadow:0 2px 2px rgba(0,0,0,.6);
  border:3px solid var(--gold);box-shadow:0 0 0 1px var(--gold-dark),inset 0 2px 0 rgba(255,255,255,.45),0 5px 10px rgba(0,0,0,.6)}
.tab.active{background:linear-gradient(var(--sapphire-hi),var(--sapphire) 48%,var(--sapphire-dark))}
.tab.idle{background:linear-gradient(var(--emerald-hi),var(--emerald) 48%,var(--emerald-dark))}
.tab-art{position:absolute;left:-6px;top:-8px;width:52px;height:52px;border-radius:50%;
  background:radial-gradient(circle at 40% 35%,#f4e3b0,#b0753a 60%,#5a2610);border:2px solid var(--gold);box-shadow:0 3px 6px rgba(0,0,0,.6)}

/* left column */
.side-panel{background:linear-gradient(#1a1d1c,var(--lacquer));border-radius:12px}
.avatar{left:24px;top:94px;width:146px;height:182px;background:linear-gradient(#2d2f31,#7d8186);border:2px solid var(--silver-dark)}
.username{left:24px;top:277px;width:146px;height:26px;font-size:15px;display:flex;align-items:center;justify-content:center;
  background:linear-gradient(#8a8d91,#3a3c3f);border-top:1px solid var(--silver)}
.profile-btn{left:22px;top:306px;width:150px;height:33px;display:flex;align-items:center;gap:26px;padding-left:8px;font-size:16px;
  background:linear-gradient(var(--sapphire-hi),var(--sapphire) 50%,var(--sapphire-dark));border-radius:3px;
  box-shadow:inset 0 1px 0 rgba(255,255,255,.5)}
.profile-icon{width:22px;height:23px;border-radius:3px;background:linear-gradient(#333,#000);border:1px solid #666}
.link-btn{left:20px;width:151px;height:31px;border-radius:10px;display:flex;align-items:center;gap:10px;padding-left:6px;font-size:11px;
  background:linear-gradient(var(--sapphire-hi),var(--sapphire) 50%,var(--sapphire-dark));
  border:1px solid var(--gold);box-shadow:inset 0 1px 0 rgba(255,255,255,.4),0 3px 6px rgba(0,0,0,.7)}
.link-icon{width:21px;height:21px;border-radius:4px;display:flex;align-items:center;justify-content:center;
  background:linear-gradient(#5d9cf5,#1d55c2);border:1px solid #fff}

/* dealers */
.dealer-frame{background:linear-gradient(var(--silver-hi),var(--silver) 40%,var(--silver-dark));border-radius:3px}
.dealer-card{position:absolute;background:#151515;border:2px solid var(--silver-dark);overflow:hidden;box-shadow:0 3px 6px rgba(0,0,0,.5)}
.dealer-photo{position:absolute;left:3px;top:3px;border-radius:8px;background:linear-gradient(160deg,#49b0f0,#0e3560 55%,#061a30);border:2px solid #3aa0f0}
.roadmap{position:absolute;top:3px;right:3px;background-color:#fff;
  background-image:linear-gradient(var(--grid) 1px,transparent 1px),linear-gradient(90deg,var(--grid) 1px,transparent 1px)}
.dealer-bar{position:absolute;left:0;right:0;bottom:0;display:flex;background:linear-gradient(#222,#000)}
.dealer-name{flex:1;padding-left:10px;display:flex;align-items:center}
.dealer-deals{display:flex;align-items:center;padding:0 8px;background:linear-gradient(#3c7ae0,#1a45a8)}

/* filter bar */
.filter-bar{left:205px;top:232px;width:977px;height:33px;border-radius:8px;
  background:linear-gradient(#4b4b4b,#0c0c0c);border:1px solid var(--gold-mid);box-shadow:0 4px 8px rgba(0,0,0,.6)}
.chip{top:237px;height:24px;border-radius:7px;color:var(--text-dark);font-size:12px;display:flex;align-items:center;justify-content:center;gap:4px;
  background:linear-gradient(var(--silver-hi),var(--silver) 50%,#9da3a9);box-shadow:inset 0 -1px 0 rgba(0,0,0,.25)}

/* table cards */
.table-card{width:281px;height:139px;border-radius:9px;overflow:hidden;
  background:linear-gradient(#000 0%,#050805 45%,#1f4a10 82%,#0a1a06 100%);
  border:3px solid var(--silver);box-shadow:0 0 0 1px var(--silver-dark),0 6px 14px rgba(0,0,0,.75)}
.tc-title{position:absolute;left:13px;top:7px;font-size:11px;color:var(--yellow);line-height:1.4}
.tc-title span{color:#fff;display:block}
.tc-comm{position:absolute;right:13px;top:7px;font-size:11px;color:var(--yellow);text-align:right;line-height:1.4}
.tc-comm span{color:#fff;display:block}
.join-coin{position:absolute;left:97px;top:9px;width:84px;height:46px;border-radius:50%;
  display:flex;align-items:center;justify-content:center;color:#7a4a00;font-size:13px;font-weight:500;
  background:radial-gradient(ellipse at 40% 30%,var(--gold-hi),var(--gold) 45%,var(--gold-mid) 75%,var(--gold-dark));
  border:2px solid #ffe07a;box-shadow:0 3px 0 var(--gold-dark),0 5px 8px rgba(0,0,0,.7)}
.felt-grid{position:absolute;left:14px;right:14px;top:62px;height:38px;display:grid;grid-template-columns:repeat(7,1fr);
  transform:perspective(160px) rotateX(28deg);transform-origin:50% 100%;
  border:1px solid #dff2c8}
.felt-grid div{border:1px solid #dff2c8;font-size:10px;font-weight:700;font-style:italic;display:flex;align-items:center;justify-content:center}
.felt-grid .b{color:var(--yellow)}
.felt-grid .p{color:#fff}
.seat-strip{position:absolute;left:5px;right:5px;bottom:5px;height:25px;display:grid;grid-template-columns:repeat(7,1fr);gap:3px}
.seat{position:relative;border:1px solid #7bd49a;border-radius:2px;
  background:
    radial-gradient(circle at 50% 36%,var(--skin) 0 4px,transparent 4.6px),
    radial-gradient(ellipse 9px 7px at 50% 100%,var(--skin) 0 96%,transparent 100%),
    linear-gradient(#2aa35a,#0b4a22)}
.seat.more{border-color:#ffe27a;background:linear-gradient(#f1c95a,#a6701a)}
.seat.more::after{content:"";position:absolute;left:50%;top:50%;width:17px;height:13px;transform:translate(-50%,-50%);
  background:linear-gradient(#fff3b8,#f4cf52);clip-path:polygon(30% 0,70% 0,70% 45%,100% 45%,50% 100%,0 45%,30% 45%)}

/* scroll + balance */
.scroll-track{left:1171px;top:300px;width:10px;height:308px;border-radius:5px;background:linear-gradient(90deg,#000,#2a2a2a,#000)}
.scroll-thumb{left:1167px;top:310px;width:18px;height:31px;border-radius:4px;background:linear-gradient(90deg,#8a8f95,#fff,#8a8f95);border:1px solid var(--gold)}
.balance{left:940px;top:639px;width:255px;height:33px;border-radius:9px;display:flex;align-items:center;font-size:15px;overflow:hidden;
  background:linear-gradient(#2c2c2c,#050505)}
.balance-label{padding:0 12px 0 17px}
.currency{height:100%;display:flex;align-items:center;padding:0 6px;font-size:10px;background:linear-gradient(var(--gold),var(--gold-dark))}
.balance-value{flex:1;padding-left:10px;font-size:14px}
</style>
</head>
<body>
<main class="lobby">
  <div class="abs brand gold-rim"><span class="brand-dot"></span><span class="brand-name">LIVE CASINO</span></div>
  <div class="abs clock">12/03/2014 &nbsp;09 : 18 AM</div>

  <div class="abs tool" style="left:1002px"><svg width="20" height="20" viewBox="0 0 20 20"><circle cx="8" cy="8" r="6" fill="none" stroke="#fff" stroke-width="2"/><path d="M12 12l6 6" stroke="#fff" stroke-width="3"/></svg></div>
  <div class="abs tool" style="left:1041px"><svg width="20" height="20" viewBox="0 0 20 20"><circle cx="10" cy="10" r="8" fill="none" stroke="#fff" stroke-width="2"/><text x="10" y="14.5" font-size="12" text-anchor="middle" fill="#fff" font-family="Roboto,sans-serif" font-weight="700">$</text></svg></div>
  <div class="abs tool" style="left:1080px"><svg width="20" height="20" viewBox="0 0 20 20" fill="none" stroke="#fff" stroke-width="2"><path d="M2 7V2h5M13 2h5v5M18 13v5h-5M7 18H2v-5"/></svg></div>
  <div class="abs tool" style="left:1119px"><svg width="20" height="20" viewBox="0 0 20 20" fill="#fff"><path d="M7 3l10-2v13h-2V5L9 6v10H7z"/><circle cx="5" cy="16" r="3"/><circle cx="14" cy="14" r="3"/></svg></div>
  <div class="abs tool close" style="left:1160px"><svg width="20" height="20" viewBox="0 0 20 20"><path d="M3 3l14 14M17 3L3 17" stroke="#fff" stroke-width="3"/></svg></div>

  <div class="abs tab active" style="left:202px;width:224px"><span class="tab-art" role="img" aria-label="Playing cards artwork"></span>Bacarat</div>
  <div class="abs tab idle" style="left:441px;width:226px"><span class="tab-art" role="img" aria-label="Cards and chips artwork"></span>Super six</div>
  <div class="abs tab idle" style="left:680px;width:225px"><span class="tab-art" role="img" aria-label="Roulette wheel artwork"></span>Roulette</div>
  <div class="abs tab idle" style="left:920px;width:224px"><span class="tab-art" role="img" aria-label="Dice artwork"></span>Sic Bo</div>

  <section class="abs side-panel gold-rim" style="left:13px;top:81px;width:172px;height:270px"></section>
  <div class="abs avatar" role="img" aria-label="Player avatar"></div>
  <div class="abs username">Xon125</div>
  <div class="abs profile-btn"><span class="profile-icon"></span>Profile</div>

  <section class="abs side-panel gold-rim" style="left:13px;top:369px;width:172px;height:255px"></section>
  <div class="abs link-btn" style="top:384px"><span class="link-icon"><svg width="12" height="12" viewBox="0 0 12 12" fill="none" stroke="#fff" stroke-width="1.6"><circle cx="2" cy="10" r="1.2" fill="#fff"/><path d="M1 5a6 6 0 0 1 6 6M1 1a10 10 0 0 1 10 10"/></svg></span>Announcements</div>
  <div class="abs link-btn" style="top:429px"><span class="link-icon"><svg width="12" height="12" viewBox="0 0 12 12"><path d="M6 1v7M6 9.5v1.5" stroke="#fff" stroke-width="2"/></svg></span>Rules &amp; Regulation</div>
  <div class="abs link-btn" style="top:476px"><span class="link-icon"><svg width="12" height="12" viewBox="0 0 12 12" fill="none" stroke="#fff" stroke-width="1.6"><circle cx="5" cy="5" r="3.5"/><path d="M7.5 7.5L11 11"/></svg></span>Quick tour</div>

  <div class="abs dealer-frame gold-rim" style="left:211px;top:98px;width:264px;height:124px">
    <div class="dealer-card" style="left:6px;top:6px;width:248px;height:108px">
      <div class="dealer-photo" role="img" aria-label="Dealer photo" style="width:86px;height:82px"></div>
      <div class="roadmap" style="left:93px;width:150px;height:82px;background-size:12.5px 12.5px"></div>
      <div class="dealer-bar" style="height:21px;font-size:11px"><span class="dealer-name">Dealer Name</span><span class="dealer-deals">Deals 999</span></div>
    </div>
  </div>

  <div class="abs dealer-frame gold-rim" style="left:496px;top:98px;width:699px;height:117px"></div>
  <div class="dealer-card" style="left:513px;top:110px;width:214px;height:92px">
    <div class="dealer-photo" role="img" aria-label="Dealer photo" style="width:68px;height:68px"></div>
    <div class="roadmap" style="left:75px;width:134px;height:68px;background-size:11px 11px"></div>
    <div class="dealer-bar" style="height:16px;font-size:8px"><span class="dealer-name">Dealer Name</span><span class="dealer-deals">Deals 999</span></div>
  </div>
  <div class="dealer-card" style="left:738px;top:110px;width:214px;height:92px">
    <div class="dealer-photo" role="img" aria-label="Dealer photo" style="width:68px;height:68px"></div>
    <div class="roadmap" style="left:75px;width:134px;height:68px;background-size:11px 11px"></div>
    <div class="dealer-bar" style="height:16px;font-size:8px"><span class="dealer-name">Dealer Name</span><span class="dealer-deals">Deals 999</span></div>
  </div>
  <div class="dealer-card" style="left:965px;top:110px;width:214px;height:92px">
    <div class="dealer-photo" role="img" aria-label="Dealer photo" style="width:68px;height:68px"></div>
    <div class="roadmap" style="left:75px;width:134px;height:68px;background-size:11px 11px"></div>
    <div class="dealer-bar" style="height:16px;font-size:8px"><span class="dealer-name">Dealer Name</span><span class="dealer-deals">Deals 999</span></div>
  </div>

  <div class="abs filter-bar"></div>
  <div class="abs chip" style="left:209px;width:145px;justify-content:flex-start;padding-left:6px;gap:16px;font-size:11px"><svg width="22" height="20" viewBox="0 0 22 20" style="background:#fff;border-radius:2px"><circle cx="11" cy="6" r="4" fill="#222"/><path d="M3 19c0-6 16-6 16 0z" fill="#222"/></svg>Multiplayer</div>
  <div class="abs chip" style="left:360px;width:285px"></div>
  <div class="abs chip" style="left:665px;width:112px;font-size:11px">Join any</div>
  <div class="abs chip" style="left:780px;width:44px">A ➔ Z</div>
  <div class="abs chip" style="left:828px;width:42px;font-weight:700">$<svg width="9" height="10" viewBox="0 0 9 10"><path d="M3 0h3v5h3L4.5 10 0 5h3z" fill="#222"/></svg></div>
  <div class="abs chip" style="left:873px;width:45px;font-weight:700">$<svg width="9" height="10" viewBox="0 0 9 10"><path d="M3 10h3V5h3L4.5 0 0 5h3z" fill="#222"/></svg></div>
  <div class="abs chip" style="left:924px;width:44px"><svg width="26" height="16" viewBox="0 0 26 16" fill="#222"><circle cx="7" cy="4" r="3"/><circle cx="13" cy="4" r="3"/><circle cx="19" cy="4" r="3"/><path d="M1 15c0-5 24-5 24 0z"/></svg></div>
  <div class="abs chip" style="left:971px;width:43px;font-size:13px">⩽ 3</div>
  <div class="abs chip" style="left:1017px;width:45px;font-size:13px">&gt; 3</div>
  <div class="abs chip" style="left:1065px;width:112px;font-size:14px">All Limits <svg width="12" height="8" viewBox="0 0 12 8"><path d="M0 0h12L6 8z" fill="#222"/></svg></div>

  <article class="abs table-card" style="left:239px;top:303px">
    <div class="tc-title">Baccarat A5-3C<span>Bet Limit</span></div>
    <div class="tc-comm">Commission 0/7<span>0/100</span></div>
    <div class="join-coin">JOIN</div>
    <div class="felt-grid"><div class="b">B</div><div class="b">B</div><div class="b">B</div><div class="b">B</div><div class="b">B</div><div class="b">B</div><div class="b">B</div><div class="p">P</div><div class="p">P</div><div class="p">P</div><div class="p">P</div><div class="p">P</div><div class="p">P</div><div class="p">P</div></div>
    <div class="seat-strip"><span class="seat"></span><span class="seat"></span><span class="seat"></span><span class="seat"></span><span class="seat"></span><span class="seat more"></span><span class="seat more"></span></div>
  </article>

  <article class="abs table-card" style="left:549px;top:303px">
    <div class="tc-title">Baccarat A5-3C<span>Bet Limit</span></div>
    <div class="tc-comm">Commission 0/7<span>0/100</span></div>
    <div class="join-coin">JOIN</div>
    <div class="felt-grid"><div class="b">B</div><div class="b">B</div><div class="b">B</div><div class="b">B</div><div class="b">B</div><div class="b">B</div><div class="b">B</div><div class="p">P</div><div class="p">P</div><div class="p">P</div><div class="p">P</div><div class="p">P</div><div class="p">P</div><div class="p">P</div></div>
    <div class="seat-strip"><span class="seat"></span><span class="seat"></span><span class="seat"></span><span class="seat"></span><span class="seat"></span><span class="seat more"></span><span class="seat more"></span></div>
  </article>

  <article class="abs table-card" style="left:859px;top:303px">
    <div class="tc-title">Baccarat A5-3C<span>Bet Limit</span></div>
    <div class="tc-comm">Commission 0/7<span>0/100</span></div>
    <div class="join-coin">JOIN</div>
    <div class="felt-grid"><div class="b">B</div><div class="b">B</div><div class="b">B</div><div class="b">B</div><div class="b">B</div><div class="b">B</div><div class="b">B</div><div class="p">P</div><div class="p">P</div><div class="p">P</div><div class="p">P</div><div class="p">P</div><div class="p">P</div><div class="p">P</div></div>
    <div class="seat-strip"><span class="seat"></span><span class="seat"></span><span class="seat"></span><span class="seat"></span><span class="seat"></span><span class="seat more"></span><span class="seat more"></span></div>
  </article>

  <article class="abs table-card" style="left:239px;top:465px">
    <div class="tc-title">Baccarat A5-3C<span>Bet Limit</span></div>
    <div class="tc-comm">Commission 0/7<span>0/100</span></div>
    <div class="join-coin">JOIN</div>
    <div class="felt-grid"><div class="b">B</div><div class="b">B</div><div class="b">B</div><div class="b">B</div><div class="b">B</div><div class="b">B</div><div class="b">B</div><div class="p">P</div><div class="p">P</div><div class="p">P</div><div class="p">P</div><div class="p">P</div><div class="p">P</div><div class="p">P</div></div>
    <div class="seat-strip"><span class="seat"></span><span class="seat"></span><span class="seat"></span><span class="seat"></span><span class="seat"></span><span class="seat more"></span><span class="seat more"></span></div>
  </article>

  <article class="abs table-card" style="left:549px;top:465px">
    <div class="tc-title">Baccarat A5-3C<span>Bet Limit</span></div>
    <div class="tc-comm">Commission 0/7<span>0/100</span></div>
    <div class="join-coin">JOIN</div>
    <div class="felt-grid"><div class="b">B</div><div class="b">B</div><div class="b">B</div><div class="b">B</div><div class="b">B</div><div class="b">B</div><div class="b">B</div><div class="p">P</div><div class="p">P</div><div class="p">P</div><div class="p">P</div><div class="p">P</div><div class="p">P</div><div class="p">P</div></div>
    <div class="seat-strip"><span class="seat"></span><span class="seat"></span><span class="seat"></span><span class="seat"></span><span class="seat"></span><span class="seat more"></span><span class="seat more"></span></div>
  </article>

  <article class="abs table-card" style="left:859px;top:465px">
    <div class="tc-title">Baccarat A5-3C<span>Bet Limit</span></div>
    <div class="tc-comm">Commission 0/7<span>0/100</span></div>
    <div class="join-coin">JOIN</div>
    <div class="felt-grid"><div class="b">B</div><div class="b">B</div><div class="b">B</div><div class="b">B</div><div class="b">B</div><div class="b">B</div><div class="b">B</div><div class="p">P</div><div class="p">P</div><div class="p">P</div><div class="p">P</div><div class="p">P</div><div class="p">P</div><div class="p">P</div></div>
    <div class="seat-strip"><span class="seat"></span><span class="seat"></span><span class="seat"></span><span class="seat"></span><span class="seat"></span><span class="seat more"></span><span class="seat more"></span></div>
  </article>

  <div class="abs scroll-track"></div>
  <div class="abs scroll-thumb"></div>

  <div class="abs balance gold-rim"><span class="balance-label">Balance</span><span class="currency">$ SGD ‹</span><span class="balance-value">999,999,999</span></div>
</main>
</body>
</html>
```